The Harrowgate

We need a APP for our members. this is a Private Bar/Venue. history of the brick building is it was built in1898 and was a gentleman club, oyster house, cigar factory and then law offices before we purchased and are beginning restoration.
the APP must include
1. direct texting to the concierge
2. calendar of events
3. Pellmont Lock To open the lock, anyone with a code can approach the door, enable their phone's Bluetooth and press the relevant address from the app.
Read more: http://www.brevinpost.example/tech/article-5521840/keyless-entry-phone-door-lock-explained.html#qq7rTb2mWx
4. Menus from various restaurants from our surrounding area
5. member name and member number to give the feel that the app is personalized
6. the members account balance
7. ability to pay their bill with credit card or pim coin monthly and automatically.
8. link to zirva with its own icon within the app.
9.the ability to reserve the room
Anything else that may of interest for our members that may be relevant that I may not have mentioned since we are new at this...
35 to 60 years of age
Club
Designer to choose colors to be used in the design.

```html
<!DOCTYPE html>
<html lang="en">
<head>
<meta charset="utf-8">
<title>The Harrowgate – Member App Screens</title>
<link href="https://fonts.googleapis.com/css2?family=Open+Sans:wght@400;600&display=swap" rel="stylesheet">
<style>
:root{
  --ink:#3b3b3b;
  --bar:#3a3a3a;
  --mid:#9c9c9c;
  --soft:#bdbdbd;
  --muted:#8c8c8c;
  --line:#9a9a9a;
  --paper:#ffffff;
  --keys:#d2d5da;
  --accent:#1a7cf5;
}
*{box-sizing:border-box;margin:0;padding:0}
html,body{width:1200px;height:1200px;overflow:hidden;background:var(--paper);font-family:"Open Sans",Arial,sans-serif}
.stage{position:absolute;left:0;top:0;width:1500px;height:1500px;transform:scale(.8);transform-origin:0 0}
.screen{position:absolute;width:283px;height:500px;overflow:hidden;background:var(--paper)}
.a{position:absolute}
.header{position:absolute;left:0;top:0;width:100%;height:53px;background:var(--bar);color:#fff;font-size:19px;display:flex;align-items:center;justify-content:center;text-align:center;line-height:22px}
.burger{position:absolute;left:15px;top:19px;width:21px;height:15px;border-top:2px solid #fff;border-bottom:2px solid #fff}
.burger::after{content:"";position:absolute;left:0;top:4.5px;width:100%;height:2px;background:#fff}
.brand{position:absolute;left:0;width:100%;text-align:center;font-size:17px;letter-spacing:3px;color:#111}
.tabs{position:absolute;left:0;top:206px;width:100%;height:35px;display:flex}
.tab{flex:1;display:flex;align-items:center;justify-content:center;color:#fff;font-size:14px;background:var(--mid)}
.tab.on{background:var(--ink)}
.label{position:absolute;left:29px;font-size:9px;color:#666}
.rule{position:absolute;left:29px;width:225px;height:1px;background:var(--line)}
.btn{position:absolute;display:flex;align-items:center;justify-content:center;color:#fff;font-size:14px;background:var(--mid);border-radius:2px}
.btn.dark{background:var(--ink)}
.band{position:absolute;left:0;width:100%;height:28px;background:var(--mid);color:#fff;font-size:13px;display:flex;align-items:center;justify-content:center}
.event{position:absolute;left:0;width:100%;height:62px;color:var(--muted);font-size:12.5px;line-height:18.5px}
.event .time{position:absolute;left:20px;top:2px;text-decoration:underline}
.event .vr{position:absolute;left:70px;top:-8px;width:1px;height:56px;background:var(--line)}
.event .txt{position:absolute;left:87px;top:2px;width:180px}
.open{position:absolute;left:0;top:82px;width:100%;height:162px;background:#4d4d4d;color:#fff;font-size:12.5px;line-height:18.5px}
.open .time{position:absolute;left:20px;top:12px;text-decoration:underline}
.open .vr{position:absolute;left:70px;top:12px;width:1px;height:140px;background:#bbb}
.open .txt{position:absolute;left:87px;top:12px;width:185px}
.opt{display:flex;align-items:center;gap:9px;line-height:18px}
.radio{width:11px;height:11px;border-radius:50%;border:1.3px solid currentColor;flex:none}
.radio.on{background:currentColor}
.bubble{position:absolute;width:157px;height:47px;padding:10px 14px;font-size:9.5px;line-height:13px;color:#fff}
.bubble.me{background:var(--ink)}
.bubble.me::after{content:"";position:absolute;right:-7px;top:26px;border:7px solid transparent;border-left-color:var(--ink);border-right:0}
.bubble.them{background:var(--mid)}
.bubble.them::after{content:"";position:absolute;left:-7px;top:26px;border:7px solid transparent;border-right-color:var(--mid);border-left:0}
.chev{position:absolute;width:9px;height:9px;border-top:1.5px solid #444;border-right:1.5px solid #444;transform:rotate(45deg)}
.keyboard{position:absolute;left:0;top:338px;width:100%;height:162px;background:var(--keys);padding:5px 3px}
.krow{display:flex;justify-content:center;gap:3.6px;margin-bottom:13px}
.key{width:24px;height:27px;background:#fff;border-radius:4px;font-size:16px;display:flex;align-items:center;justify-content:center;color:#111}
.key.fn{background:#b0b5bd;width:32px;font-size:11px}
.card{position:absolute;background:var(--mid);color:#fff;font-size:13px;line-height:18.3px;padding:12px 10px}
.panel{position:absolute;background:var(--ink);color:#fff}
.check{display:flex;align-items:center;gap:8px;font-size:13px;line-height:18.3px}
.hist{position:absolute;left:20px;width:241px;font-size:12.5px;line-height:18.3px;color:var(--muted)}
.hist div{display:flex;justify-content:space-between}
.field{position:absolute;height:18px;border:1px solid var(--line);border-radius:3px}
.flabel{position:absolute;font-size:12.5px;color:var(--muted)}
.tiny{position:absolute;font-size:6px;color:var(--muted);text-align:center;width:50px}
.nav{position:absolute;left:18px;font-size:13px;color:var(--muted)}
</style>
</head>
<body>
<div class="stage">

<!-- Sign in -->
<section class="screen" style="left:0;top:0">
  <div class="brand" style="top:112px">THE HARROWGATE</div>
  <div class="tabs"><div class="tab on">Sign in</div><div class="tab">Sign up</div></div>
  <div class="label" style="top:267px">Username:</div><div class="rule" style="top:294px"></div>
  <div class="label" style="top:329px">Password:</div>
  <div class="a" style="right:29px;top:331px;font-size:6px;color:#999">Forgot password?</div>
  <div class="rule" style="top:356px"></div>
  <div class="btn" style="left:20px;top:389px;width:242px;height:60px">Sign in</div>
</section>

<!-- Sign up -->
<section class="screen" style="left:283px;top:0">
  <div class="brand" style="top:112px">THE HARROWGATE</div>
  <div class="tabs"><div class="tab">Sign in</div><div class="tab on">Sign up</div></div>
  <div class="label" style="top:267px">Username:</div><div class="rule" style="top:294px"></div>
  <div class="label" style="top:315px">Email:</div><div class="rule" style="top:342px"></div>
  <div class="label" style="top:362px">Password:</div><div class="rule" style="top:389px"></div>
  <div class="btn" style="left:20px;top:422px;width:242px;height:60px">Sign up</div>
</section>

<!-- Calendar -->
<section class="screen" style="left:566px;top:0">
  <div class="header"><span class="burger"></span>CALENDAR</div>
  <div class="band" style="top:53px">Today</div>
  <div class="event" style="top:95px"><span class="time">21.00</span><span class="vr"></span><div class="txt">Name of the Event:<br>Text text text text text text<br>text text text text text.</div></div>
  <div class="event" style="top:165px"><span class="time">22.00</span><span class="vr"></span><div class="txt">Name of the Event:<br>Text text text text text text<br>text text text text text.</div></div>
  <div class="band" style="top:241px">Monday</div>
  <div class="event" style="top:283px"><span class="time">21.00</span><span class="vr"></span><div class="txt">Name of the Event:<br>Text text text text text text<br>text text text text text.</div></div>
  <div class="event" style="top:353px"><span class="time">22.00</span><span class="vr"></span><div class="txt">Name of the Event:<br>Text text text text text text<br>text text text text text.</div></div>
  <div class="band" style="top:429px">Tuesday</div>
  <div class="event" style="top:470px"><span class="time">21.00</span><span class="vr"></span><div class="txt">Name of the Event:<br>Text text text text text text</div></div>
</section>

<!-- Calendar, event open -->
<section class="screen" style="left:849px;top:0">
  <div class="header"><span class="burger"></span>CALENDAR</div>
  <div class="band" style="top:53px">Today</div>
  <div class="open"><span class="time">21.00</span><span class="vr"></span>
    <div class="txt">Name of the Event:<br>Text text text text text text<br>text text text text text.
      <div style="margin-top:9px">
        <div class="opt"><span class="radio on"></span>I'm Attending</div>
        <div class="opt"><span class="radio"></span>Maybe</div>
        <div class="opt"><span class="radio"></span>I have to Decline</div>
      </div>
    </div>
  </div>
  <div class="event" style="top:251px"><span class="time">22.00</span><span class="vr"></span><div class="txt">Name of the Event:<br>Text text text text text text<br>text text text text text.</div></div>
  <div class="band" style="top:326px">Monday</div>
  <div class="event" style="top:368px"><span class="time">21.00</span><span class="vr"></span><div class="txt">Name of the Event:<br>Text text text text text text<br>text text text text text.</div></div>
  <div class="event" style="top:438px"><span class="time">22.00</span><span class="vr"></span><div class="txt">Name of the Event:<br>Text text text text text text<br>text text text text text.</div></div>
</section>

<!-- Concierge chat -->
<section class="screen" style="left:1132px;top:0">
  <div class="header"><span class="burger"></span>CONCIERGE</div>
  <div class="bubble me" style="left:96px;top:73px">Text text text text.<br>Text text.</div>
  <div class="bubble them" style="left:27px;top:134px">Text text text text.<br>Text text.</div>
  <div class="bubble me" style="left:96px;top:195px">Text text text text.<br>Text text.</div>
  <div class="bubble them" style="left:27px;top:256px">Text text text text.<br>Text text.</div>
  <div class="bubble me" style="left:96px;top:317px">Text text text text.<br>Text text.</div>
  <div class="bubble them" style="left:27px;top:378px">Text text text text.<br>Text text.</div>
  <div class="a" style="left:0;top:449px;width:100%;height:1px;background:var(--soft)"></div>
  <div class="a" style="left:12px;top:454px;font-size:12.5px;color:var(--muted)">Reply</div>
  <div class="a" style="left:0;top:475px;width:100%;height:1px;background:var(--soft)"></div>
  <div class="a" style="left:12px;top:479px;font-size:12.5px;color:var(--muted)">Text text text text.</div>
  <span class="chev" style="left:256px;top:483px"></span>
</section>

<!-- Concierge with keyboard -->
<section class="screen" style="left:0;top:500px">
  <div class="header"><span class="burger"></span>CONCIERGE</div>
  <div class="bubble me" style="left:97px;top:73px">Text text text text.<br>Text text.</div>
  <div class="bubble them" style="left:28px;top:134px">Text text text text.<br>Text text.</div>
  <div class="bubble me" style="left:97px;top:195px">Text text text text.<br>Text text.</div>
  <div class="bubble them" style="left:28px;top:256px">Text text text text.<br>Text text.</div>
  <div class="a" style="left:0;top:312px;width:100%;height:1px;background:var(--soft)"></div>
  <div class="a" style="left:13px;top:317px;font-size:12.5px;color:var(--muted)">Text text text text.</div>
  <span class="chev" style="left:258px;top:321px"></span>
  <div class="keyboard">
    <div class="krow"><span class="key">Q</span><span class="key">W</span><span class="key">E</span><span class="key">R</span><span class="key">T</span><span class="key">Y</span><span class="key">U</span><span class="key">I</span><span class="key">O</span><span class="key">P</span></div>
    <div class="krow"><span class="key">A</span><span class="key">S</span><span class="key">D</span><span class="key">F</span><span class="key">G</span><span class="key">H</span><span class="key">J</span><span class="key">K</span><span class="key">L</span></div>
    <div class="krow" style="justify-content:space-between;padding:0 2px">
      <span class="key fn" style="width:30px">⇧</span>
      <span style="display:flex;gap:3.6px"><span class="key">Z</span><span class="key">X</span><span class="key">C</span><span class="key">V</span><span class="key">B</span><span class="key">N</span><span class="key">M</span></span>
      <span class="key fn" style="width:30px">⌫</span>
    </div>
    <div class="krow" style="gap:4px;margin:0">
      <span class="key fn" style="width:30px;height:30px">123</span>
      <span class="key fn" style="width:30px;height:30px">◍</span>
      <span class="key fn" style="width:30px;height:30px;background:#fff">•</span>
      <span class="key" style="width:108px;height:30px;font-size:11px">space</span>
      <span class="key" style="width:66px;height:30px;font-size:11px;background:var(--accent);color:#fff">Search</span>
    </div>
  </div>
</section>

<!-- Entrance -->
<section class="screen" style="left:283px;top:500px">
  <div class="header" style="font-size:16px"><span class="burger"></span>THE HARROWGATE<br>ENTRANCE</div>
  <svg class="a" style="left:35px;top:87px" width="212" height="212" viewBox="0 0 212 212" aria-hidden="true">
    <circle cx="106" cy="106" r="92" fill="none" stroke="var(--mid)" stroke-width="28"/>
  </svg>
  <div class="a" style="left:0;top:166px;width:100%;text-align:center;font-size:19px;line-height:27px;color:#555">TOUCH<br>HERE</div>
  <div class="a" style="left:0;top:337px;width:100%;text-align:center;font-size:12.5px;line-height:19px;color:var(--muted)">Adress of the bar<br>Phone Number</div>
</section>

<!-- Menus -->
<section class="screen" style="left:566px;top:500px">
  <div class="header"><span class="burger"></span>MENUS</div>
  <div class="brand" style="top:113px">THE HARROWGATE</div>
  <div class="card" style="left:13px;top:170px;width:119px;height:153px">Resturant name:<br>- menu<br>- menu<br>- menu<br>- menu<br>- menu<br>- ...</div>
  <div class="card" style="left:147px;top:170px;width:120px;height:153px">Resturant name:<br>- menu<br>- menu<br>- menu<br>- menu<br>- menu<br>- ...</div>
  <div class="card" style="left:13px;top:338px;width:119px;height:154px">Resturant name:<br>- menu<br>- menu<br>- menu<br>- menu<br>- menu<br>- ...</div>
  <div class="card" style="left:147px;top:338px;width:120px;height:154px">Resturant name:<br>- menu<br>- menu<br>- menu<br>- menu<br>- menu<br>- ...</div>
</section>

<!-- Menus, order -->
<section class="screen" style="left:849px;top:500px">
  <div class="card" style="left:13px;top:40px;width:120px;height:120px;padding-top:16px">- menu<br>- menu<br>- menu<br>- menu<br>- ...</div>
  <div class="card" style="left:147px;top:40px;width:121px;height:120px;padding-top:16px">- menu<br>- menu<br>- menu<br>- menu<br>- ...</div>
  <div class="header"><span class="burger"></span>MENUS</div>
  <div class="panel" style="left:13px;top:174px;width:255px;height:305px;padding:13px 10px">
    <div style="font-size:13px;line-height:18.3px">Resturant name:</div>
    <div class="check"><span class="radio on"></span>Lorem Ipsum</div>
    <div class="check"><span class="radio"></span>Lorem Ipsum</div>
    <div class="check"><span class="radio"></span>Lorem Ipsum</div>
    <div class="check"><span class="radio"></span>Lorem Ipsum</div>
    <div class="check"><span class="radio"></span>Lorem Ipsum</div>
    <div class="check"><span class="radio on"></span>Lorem Ipsum</div>
    <div class="check"><span class="radio"></span>Lorem Ipsum</div>
    <div class="check"><span class="radio"></span>Lorem Ipsum</div>
    <div class="check"><span class="radio"></span>Lorem Ipsum</div>
    <div class="check"><span class="radio on"></span>Lorem Ipsum</div>
    <div class="check"><span class="radio"></span>Lorem Ipsum</div>
  </div>
  <div class="btn" style="left:28px;top:423px;width:225px;height:42px;font-size:19px">ORDER</div>
</section>

<!-- Balance -->
<section class="screen" style="left:1132px;top:500px">
  <div class="header"><span class="burger"></span>BALANCE</div>
  <div class="panel" style="left:20px;top:73px;width:241px;height:176px">
    <div class="a" style="left:13px;top:19px;font-size:13px">Current Balance:</div>
    <div class="a" style="left:0;top:44px;width:100%;text-align:center;font-size:35px">29.00 $</div>
    <div class="a" style="left:13px;top:109px;font-size:9px">Last Month:</div>
    <div class="a" style="left:151px;top:109px;font-size:9px">Bill:</div>
    <div class="a" style="left:13px;top:128px;font-size:23px">10.00 $</div>
    <div class="a" style="left:145px;top:128px;font-size:23px">27.00 $</div>
  </div>
  <div class="hist" style="top:271px">
    <div>History:</div>
    <div><span>- Text text</span><span>- 5.00 $</span></div>
    <div><span>- Text</span><span>- 6.00 $</span></div>
    <div><span>- Text text text</span><span>- 8.00 $</span></div>
    <div><span>- Text</span><span>+ 50.00 $</span></div>
    <div><span>- Text</span><span>- 15.00 $</span></div>
    <div><span>- Text text text</span><span>- 7.00 $</span></div>
    <div><span>- Text</span><span>- 2.00 $</span></div>
    <div><span>- Text</span><span>+ 25.00 $</span></div>
    <div><span>- Text text</span><span>- 5.00 $</span></div>
  </div>
</section>

<!-- Bill -->
<section class="screen" style="left:0;top:1000px">
  <div class="header"><span class="burger"></span>BILL</div>
  <div class="btn" style="left:20px;top:73px;width:242px;height:54px">Connect your Credit Card.</div>
  <div class="btn" style="left:20px;top:148px;width:242px;height:54px">Connect your Pim Coin.</div>
  <div class="a" style="left:20px;top:224px;font-size:12.5px;color:var(--muted)">Bill:</div>
  <div class="a" style="right:21px;top:224px;font-size:12.5px;color:var(--muted)">27.00 $</div>
</section>

<!-- Bill, card form -->
<section class="screen" style="left:283px;top:1000px">
  <div class="header"><span class="burger"></span>BILL</div>
  <div class="btn dark" style="left:20px;top:73px;width:242px;height:54px">Connect your Credit Card.</div>
  <div class="flabel" style="left:20px;top:142px">Card number:</div>
  <div class="field" style="left:20px;top:166px;width:242px"></div>
  <div class="flabel" style="left:20px;top:192px">Card expire date:</div>
  <div class="field" style="left:20px;top:216px;width:51px"></div>
  <div class="field" style="left:78px;top:216px;width:51px"></div>
  <div class="field" style="left:136px;top:216px;width:51px"></div>
  <div class="tiny" style="left:20px;top:235px">dd</div><div class="tiny" style="left:78px;top:235px">mm</div><div class="tiny" style="left:136px;top:235px">yy</div>
  <div class="flabel" style="left:20px;top:250px">CVC:</div>
  <div class="field" style="left:20px;top:274px;width:51px"></div>
  <div class="a" style="left:76px;top:278px;font-size:6px;color:var(--muted)">?</div>
  <div class="flabel" style="left:20px;top:300px">Owner:</div>
  <div class="field" style="left:20px;top:324px;width:242px"></div>
  <div class="btn" style="left:20px;top:362px;width:242px;height:54px">Connect</div>
</section>

<!-- Ride link -->
<section class="screen" style="left:566px;top:1000px">
  <div class="header"><span class="burger"></span>ZIRVA</div>
  <svg class="a" style="left:107px;top:183px" width="68" height="68" viewBox="0 0 68 68" aria-hidden="true"><circle cx="34" cy="34" r="34" fill="#000"/></svg>
  <div class="a" style="left:0;top:272px;width:100%;text-align:center;font-size:44px;letter-spacing:6px;color:#000">ZIRVA</div>
  <div class="a" style="left:0;top:456px;width:100%;text-align:center;font-size:13px;color:var(--muted)">Open ZIRVA App</div>
</section>

<!-- Conference room -->
<section class="screen" style="left:849px;top:1000px">
  <div class="header" style="font-size:17px"><span class="burger"></span>CONFERENCE ROOM</div>
  <div class="flabel" style="left:20px;top:75px">Name:</div>
  <div class="field" style="left:20px;top:98px;width:241px"></div>
  <div class="flabel" style="left:20px;top:124px">Surname:</div>
  <div class="field" style="left:20px;top:147px;width:241px"></div>
  <div class="flabel" style="left:20px;top:174px">From:</div>
  <div class="field" style="left:20px;top:197px;width:51px"></div><div class="field" style="left:78px;top:197px;width:51px"></div><div class="field" style="left:136px;top:197px;width:51px"></div>
  <div class="tiny" style="left:20px;top:216px">dd</div><div class="tiny" style="left:78px;top:216px">mm</div><div class="tiny" style="left:136px;top:216px">yy</div>
  <div class="flabel" style="left:20px;top:232px">To:</div>
  <div class="field" style="left:20px;top:255px;width:51px"></div><div class="field" style="left:78px;top:255px;width:51px"></div><div class="field" style="left:136px;top:255px;width:51px"></div>
  <div class="tiny" style="left:20px;top:274px">dd</div><div class="tiny" style="left:78px;top:274px">mm</div><div class="tiny" style="left:136px;top:274px">yy</div>
  <div class="flabel" style="left:20px;top:290px">Email:</div>
  <div class="field" style="left:20px;top:313px;width:241px"></div>
  <div class="flabel" style="left:20px;top:340px">People:</div>
  <div class="field" style="left:20px;top:363px;width:51px"></div>
  <div class="btn" style="left:22px;top:418px;width:240px;height:54px;font-size:13px">Reserve the Room</div>
</section>

<!-- Navigation drawer -->
<section class="screen" style="left:1132px;top:1000px">
  <div class="a" style="left:0;top:0;width:100%;height:53px;background:var(--bar)"></div>
  <div class="a" style="left:0;top:53px;width:100%;height:447px;background:#c4c4c4"></div>
  <div class="a" style="left:232px;top:99px;width:29px;height:17px;border:1px solid #999"></div>
  <div class="a" style="left:232px;top:148px;width:29px;height:17px;border:1px solid #999"></div>
  <div class="a" style="left:232px;top:314px;width:29px;height:17px;border:1px solid #999"></div>
  <div class="a" style="left:232px;top:418px;width:30px;height:54px;background:var(--mid)"></div>
  <nav class="a" style="left:0;top:0;width:232px;height:500px;background:var(--paper)">
    <div class="brand" style="top:60px;font-size:15.5px;letter-spacing:2.5px">THE HARROWGATE</div>
    <div class="a" style="left:16px;top:110px;width:200px;height:1.5px;background:#222"></div>
    <div class="nav" style="top:122px">TestAccount</div>
    <div class="a" style="left:16px;top:150px;width:200px;height:1.5px;background:#222"></div>
    <div class="nav" style="top:163px">Calendar</div>
    <div class="nav" style="top:195px">Concierge</div>
    <div class="nav" style="top:227px">The Harrowgate Entrance</div>
    <div class="nav" style="top:259px">Menus</div>
    <div class="nav" style="top:291px">Balance</div>
    <div class="nav" style="top:323px">Bill</div>
    <div class="nav" style="top:355px">Zirva</div>
    <div class="a" style="left:0;top:375px;width:100%;height:37px;background:var(--ink)"></div>
    <div class="nav" style="top:386px;color:#fff">Conference Room</div>
    <div class="nav" style="top:419px">Settings</div>
    <div class="nav" style="top:451px">Sign out</div>
  </nav>
</section>

</div>
</body>
</html>
```